Software as a Service to manage Home Care Management

We need a web site designed for Home Care Management Software as a Service product, that facilitates Home Care organizations to manage and schedule carers to visit client homes. We want a modern look and feel using our existing logo.

Target Market(s)

Home Care Management organizations. Product is similar to: https://carelarkly.io/

Coding

Coded - Design and coding required

Number of Pages Required

3 page

```html
<!DOCTYPE html>
<html lang="en">
<head>
<meta charset="utf-8">
<title>Visitwell – Home Care Management</title>
<link rel="stylesheet" href="https://fonts.googleapis.com/css2?family=Cinzel:wght@400;700&family=Open+Sans:wght@400;600;700&display=swap">
<style>
:root{
  --pink:#f0246d;
  --ink:#222;
  --text:#555;
  --line:#dcdcdc;
  --grey-bg:#f3f3f3;
  --dark:#111;
  --darker:#070707;
  --white:#fff;
}
*{box-sizing:border-box;margin:0;padding:0}
html,body{width:1200px;height:4577px;overflow:hidden}
body{position:relative;font-family:"Open Sans",sans-serif;color:var(--text);background:var(--white)}
.abs{position:absolute}
.accent{color:var(--pink)}

/* header */
.topbar{left:350px;top:0;width:530px;height:48px;background:var(--dark);clip-path:polygon(22px 0,100% 0,100% 100%,0 100%)}
.topbar .phone{position:absolute;left:48px;top:13px;color:#fff;font-weight:700;font-size:17px;display:flex;gap:10px;align-items:center}
.topbar .socials{position:absolute;left:272px;top:18px;display:flex;gap:22px}
.topbar .socials span{width:11px;height:11px;border-radius:50%;background:#fff}
.topbar .lang{position:absolute;left:462px;top:13px;color:#ccc;font-size:15px}
.demo-btn{left:880px;top:0;width:230px;height:48px;background:var(--pink);color:#fff;font-weight:700;font-size:17px;display:flex;align-items:center;justify-content:center}
.logo{left:90px;top:32px;display:flex;align-items:center;gap:10px}
.logo .mark{width:40px;height:40px;border-radius:50%;background:var(--pink)}
.logo .name{font-family:"Cinzel",serif;font-size:24px;color:#333;line-height:1}
.logo .tag{font-size:8px;letter-spacing:2px;color:#888;text-transform:uppercase}
.nav{left:410px;top:68px;display:flex;gap:52px;font-family:"Cinzel",serif;font-size:17px;color:#333}
.nav .active{color:var(--pink)}

/* hero */
.hero{left:0;top:107px;width:1200px;height:529px;background:linear-gradient(100deg,#cfcac3 0%,#e9e4dc 40%,#f4f1ea 70%,#dfe3d4 100%)}
.hero-title{left:0;top:270px;width:1200px;text-align:center;font-family:"Cinzel",serif;font-weight:700;font-size:64px;color:#222}
.hero-sub{left:0;top:350px;width:1200px;text-align:center;font-family:"Cinzel",serif;font-size:27px;color:#222}
.hero-btn{left:491px;top:410px;width:218px;height:48px;background:var(--pink);color:#fff;font-weight:700;font-size:16px;display:flex;align-items:center;justify-content:center;border-radius:3px}
.dots{left:560px;top:595px;display:flex;gap:10px}
.dots span{width:12px;height:12px;border-radius:50%;background:#fff}
.dots span:first-child{background:var(--pink)}

/* feature */
.feature-circle{left:128px;top:750px;width:426px;height:426px;border-radius:50%;background:#e9e9e9}
.app-shot{left:226px;top:758px;width:232px;height:468px;border-radius:34px;background:linear-gradient(180deg,#f0246d 0%,#f0246d 30%,#f4f4f4 30%,#ececec 100%)}
.feat-h1{left:640px;top:762px;font-family:"Cinzel",serif;font-size:38px;color:#222}
.feat-h2{left:640px;top:804px;font-family:"Cinzel",serif;font-size:38px;color:var(--pink)}
.checks{left:640px;top:884px;list-style:none;font-size:16px;color:#555}
.checks li{height:37.5px;display:flex;gap:22px;align-items:center}
.checks svg{flex:none}
.read-btn{left:641px;top:1177px;width:136px;height:39px;background:var(--pink);color:#fff;font-weight:700;font-size:14px;display:flex;align-items:center;justify-content:center;border-radius:3px}

/* made for */
.sec-title{left:0;width:1200px;text-align:center;font-family:"Cinzel",serif;font-size:36px;color:#222;font-weight:400}
.sec-para{left:110px;width:980px;text-align:center;font-size:15.5px;line-height:30px;color:#555}
.card{top:1504px;width:320px;height:423px;border:1px solid var(--line);background:#fff;text-align:center}
.card .ph{height:215px}
.card h3{margin-top:16px;font-size:21px;font-weight:700;color:#222}
.card p{margin:12px 22px 0;font-size:15.5px;line-height:30px;color:#777}
.card .more{margin-top:18px;font-weight:700;font-size:15px;color:var(--pink)}

/* numbers */
.numbers{left:0;top:2023px;width:1200px;height:612px;background:linear-gradient(180deg,#f0246d 0%,#e8336f 45%,#ef2166 100%)}
.numbers .sec-title,.numbers .sec-para{color:#fff}
.stat{width:184px;height:184px;border:2px solid #fff;border-radius:50%;color:#fff;font-size:50px;font-weight:600;display:flex;align-items:center;justify-content:center}
.stat-text{width:300px;text-align:center;color:#fff;font-size:16px;line-height:26px}

/* partners */
.partners{left:90px;top:2800px;width:1020px;display:flex;justify-content:space-between;align-items:center;color:#8a8a8a}
.partners span{font-size:30px;font-weight:700;letter-spacing:1px}

/* testimonials */
.testi-bg{left:0;top:2969px;width:1200px;height:330px;background:var(--grey-bg)}
.tcard{top:3124px;width:328px;height:325px;background:#fff;box-shadow:0 4px 18px rgba(0,0,0,.1);text-align:center}
.tcard .av{width:106px;height:106px;border-radius:50%;background:#8a6f5c;margin:20px auto 0}
.tcard p{margin:24px 12px 0;font-size:14px;line-height:30px;color:#555}
.tcard .who{margin-top:12px;font-family:"Cinzel",serif;font-size:19px;color:#777}

/* contact */
.dark-bg{left:0;top:3814px;width:1200px;height:763px;background:var(--dark)}
.contact-card{left:91px;top:3551px;width:1020px;height:515px;background:#fff;box-shadow:0 4px 22px rgba(0,0,0,.12)}
.contact-photo{left:601px;top:3551px;width:510px;height:515px;background:linear-gradient(120deg,#6e625a 0%,#a79a8e 40%,#d8cfc5 75%,#efe9e2 100%)}
.contact-h{left:126px;top:3630px;font-family:"Cinzel",serif;font-size:38px;color:#222;font-weight:400}
.field{height:43px;border:1px solid #ccc;font-size:14px;color:#888;padding:12px 12px}
.send-btn{left:126px;top:3940px;width:137px;height:35px;background:var(--pink);color:#fff;font-weight:700;font-size:14px;display:flex;align-items:center;justify-content:center;border-radius:3px}

.info{top:4140px;display:flex;gap:14px;align-items:center;color:#fff;font-size:15px;line-height:24px}
.info .ic{width:40px;height:40px;border-radius:50%;background:var(--pink);display:flex;align-items:center;justify-content:center;flex:none}

.fcol{top:4290px;color:#fff}
.fcol h4{font-weight:400;font-size:22px;margin-bottom:22px}
.fcol li{list-style:none;font-size:13px;line-height:27px}
.news-input{left:788px;top:4349px;width:255px;height:43px;background:#fff;color:#666;font-size:13px;padding:13px 16px}
.news-btn{left:1043px;top:4349px;width:47px;height:43px;background:var(--pink);display:flex;align-items:center;justify-content:center}

.bottom{left:0;top:4527px;width:1200px;height:50px;background:var(--darker);color:#ccc;font-size:13px}
.bottom .copy{position:absolute;left:103px;top:17px}
.bottom .connect{position:absolute;left:878px;top:17px;display:flex;gap:14px;align-items:center}
.bottom .connect i{display:block;width:10px;height:10px;background:#fff;border-radius:50%}
.bottom .code{position:absolute;left:1160px;top:19px;font-size:11px}
</style>
</head>
<body>

<!-- header -->
<div class="abs logo"><div class="mark"></div><div><div class="name">Visitwell</div><div class="tag">Home care management</div></div></div>
<div class="abs topbar">
  <div class="phone"><svg width="16" height="16" viewBox="0 0 24 24"><path fill="#fff" d="M6.6 10.8a15 15 0 0 0 6.6 6.6l2.2-2.2c.3-.3.7-.4 1-.2 1.1.4 2.3.6 3.6.6.6 0 1 .4 1 1V20c0 .6-.4 1-1 1A17 17 0 0 1 3 4c0-.6.4-1 1-1h3.5c.6 0 1 .4 1 1 0 1.3.2 2.5.6 3.6.1.3 0 .7-.2 1z"/></svg>(555) 204-7730</div>
  <div class="socials"><span></span><span></span><span></span><span></span></div>
  <div class="lang">En ⌄</div>
</div>
<div class="abs demo-btn">Book a Free Demo</div>
<nav class="abs nav"><span class="active">Home</span><span>Product</span><span>Pricing</span><span>Blog</span><span>FAQ</span><span>Contact Us</span></nav>

<!-- hero -->
<div class="abs hero" role="img" aria-label="Photo of a carer in a white coat sitting with an elderly woman in a bright living room"></div>
<h1 class="abs hero-title">VISITWELL</h1>
<div class="abs hero-sub">Home Care Management</div>
<div class="abs hero-btn">SEE HOW IT WORKS</div>
<div class="abs dots"><span></span><span></span><span></span><span></span></div>

<!-- feature -->
<div class="abs feature-circle"></div>
<div class="abs app-shot" role="img" aria-label="Screenshot of the mobile app on a phone showing the visits schedule"></div>
<div class="abs feat-h1">Optimised</div>
<div class="abs feat-h2">Home Care Software</div>
<ul class="abs checks">
  <li><svg width="16" height="16" viewBox="0 0 16 16"><circle cx="8" cy="8" r="8" fill="#f0246d"/><path d="M4.5 8.2l2.3 2.2 4.6-4.6" stroke="#fff" stroke-width="1.8" fill="none"/></svg>Lorem ipsum dolor sit amet, consectetur adipiscing</li>
  <li><svg width="16" height="16" viewBox="0 0 16 16"><circle cx="8" cy="8" r="8" fill="#f0246d"/><path d="M4.5 8.2l2.3 2.2 4.6-4.6" stroke="#fff" stroke-width="1.8" fill="none"/></svg>Sed ut perspiciatis unde omnis iste</li>
  <li><svg width="16" height="16" viewBox="0 0 16 16"><circle cx="8" cy="8" r="8" fill="#f0246d"/><path d="M4.5 8.2l2.3 2.2 4.6-4.6" stroke="#fff" stroke-width="1.8" fill="none"/></svg>Duis aute irure dolor in reprehenderit</li>
  <li><svg width="16" height="16" viewBox="0 0 16 16"><circle cx="8" cy="8" r="8" fill="#f0246d"/><path d="M4.5 8.2l2.3 2.2 4.6-4.6" stroke="#fff" stroke-width="1.8" fill="none"/></svg>At vero eos et accusamus et iusto odio dignissimos</li>
  <li><svg width="16" height="16" viewBox="0 0 16 16"><circle cx="8" cy="8" r="8" fill="#f0246d"/><path d="M4.5 8.2l2.3 2.2 4.6-4.6" stroke="#fff" stroke-width="1.8" fill="none"/></svg>On the other hand, we denounce with righteous</li>
  <li><svg width="16" height="16" viewBox="0 0 16 16"><circle cx="8" cy="8" r="8" fill="#f0246d"/><path d="M4.5 8.2l2.3 2.2 4.6-4.6" stroke="#fff" stroke-width="1.8" fill="none"/></svg>Sed ut perspiciatis unde omnis iste natus</li>
  <li><svg width="16" height="16" viewBox="0 0 16 16"><circle cx="8" cy="8" r="8" fill="#f0246d"/><path d="M4.5 8.2l2.3 2.2 4.6-4.6" stroke="#fff" stroke-width="1.8" fill="none"/></svg>Excepteur sint occaecat cupidatat non proident</li>
</ul>
<div class="abs read-btn">Read More</div>

<!-- made for -->
<h2 class="abs sec-title" style="top:1340px">We have made <span class="accent">Visitwell...</span></h2>
<p class="abs sec-para" style="top:1405px">Lorem ipsum dolor sit amet, consectetur adipiscing elit, sed do eiusmod tempor incididunt ut labore et dolore magna aliqua. Ut enim ad minim veniam, quis nostrud exercitation ullamco laboris nisi ut aliquip ex ea commodo consequat.</p>
<div class="abs card" style="left:89px"><div class="ph" role="img" aria-label="Photo of a carer with a man in a wheelchair in a park" style="background:linear-gradient(160deg,#6e7a3e,#b79a6a 60%,#8a7a5a)"></div><h3>For Managers</h3><p>Lorem ipsum dolor sit amet, consectetur adipiscing elit, sed do eiusmod tempor incididunt ut labore</p><div class="more">LEARN MORE »</div></div>
<div class="abs card" style="left:441px"><div class="ph" role="img" aria-label="Photo of a carer helping an elderly woman at a kitchen table" style="background:linear-gradient(160deg,#c9c2b6,#e6dfd3 55%,#6f7f9a)"></div><h3>For Carers</h3><p>Lorem ipsum dolor sit amet, consectetur adipiscing elit, sed do eiusmod tempor incididunt ut labore</p><div class="more">LEARN MORE »</div></div>
<div class="abs card" style="left:791px"><div class="ph" role="img" aria-label="Photo of a carer talking with an elderly woman in a care home lounge" style="background:linear-gradient(160deg,#e5e3dd,#cfd4cf 50%,#5f9a96)"></div><h3>For Clients and Families</h3><p>Lorem ipsum dolor sit amet, consectetur adipiscing elit, sed do eiusmod tempor incididunt ut labore</p><div class="more">LEARN MORE »</div></div>

<!-- numbers -->
<div class="abs numbers" role="img" aria-label="Pink tinted photo of a carer with an elderly client">
  <h2 class="abs sec-title" style="top:85px">Success in <b>numbers</b></h2>
  <p class="abs sec-para" style="top:152px">Lorem ipsum dolor sit amet, consectetur adipiscing elit, sed do eiusmod tempor incididunt ut labore et dolore magna aliqua. Ut enim ad minim veniam, quis nostrud exercitation ullamco laboris nisi ut aliquip ex ea commodo consequat. Duis aute irure dolor in reprehenderit in voluptate velit esse cillum dolore eu fugiat nulla pariatur.</p>
  <div class="abs stat" style="left:168px;top:271px">13M</div>
  <div class="abs stat" style="left:507px;top:271px">96%</div>
  <div class="abs stat" style="left:848px;top:271px">17K</div>
  <div class="abs stat-text" style="left:110px;top:473px">Lorem ipsum dolor sit amet, consectetur adipiscing</div>
  <div class="abs stat-text" style="left:449px;top:473px">Lorem ipsum dolor sit amet, consectetur adipiscing</div>
  <div class="abs stat-text" style="left:790px;top:473px">Lorem ipsum dolor sit amet, consectetur adipiscing</div>
</div>

<!-- partners -->
<h2 class="abs sec-title" style="top:2718px">Working in <span class="accent">association with</span></h2>
<div class="abs partners"><span>BIGFIELD</span><span>nimbo.</span><span style="font-weight:400">LUMORA</span><span style="font-weight:400">VERANTIS</span><span style="font-weight:400">sproutline</span></div>

<!-- testimonials -->
<div class="abs testi-bg"></div>
<h2 class="abs sec-title" style="top:3050px;font-weight:700">Testimonials</h2>
<div class="abs tcard" style="left:91px"><div class="av" role="img" aria-label="Portrait of a customer"></div><p>Lorem ipsum dolor sit amet, consectetur adipiscing elit, sed do eiusmod tempor incididunt ut labore et dolore magna aliqua. Ut enim ad minim veniam, quis nostrud</p><div class="who">Kate Marlow</div></div>
<div class="abs tcard" style="left:437px"><div class="av" role="img" aria-label="Portrait of a customer" style="background:#b58a6a"></div><p>Lorem ipsum dolor sit amet, consectetur adipiscing elit, sed do eiusmod tempor incididunt ut labore et dolore magna aliqua. Ut enim ad minim veniam, quis nostrud</p><div class="who">Henry Hale</div></div>
<div class="abs tcard" style="left:782px"><div class="av" role="img" aria-label="Portrait of a customer" style="background:#5c4536"></div><p>Lorem ipsum dolor sit amet, consectetur adipiscing elit, sed do eiusmod tempor incididunt ut labore et dolore magna aliqua. Ut enim ad minim veniam, quis nostrud</p><div class="who">Grace Holt</div></div>

<!-- contact -->
<div class="abs dark-bg"></div>
<div class="abs contact-card"></div>
<div class="abs contact-photo" role="img" aria-label="Photo of a carer with a smiling elderly woman"></div>
<h2 class="abs contact-h">Get In <b class="accent">Touch</b></h2>
<div class="abs field" style="left:126px;top:3712px;width:212px">Name</div>
<div class="abs field" style="left:350px;top:3712px;width:212px">Phone</div>
<div class="abs field" style="left:126px;top:3767px;width:212px">Email</div>
<div class="abs field" style="left:350px;top:3767px;width:212px">Address</div>
<div class="abs field" style="left:126px;top:3824px;width:436px;height:104px">Message</div>
<div class="abs send-btn">Send Message</div>

<div class="abs info" style="left:89px"><div class="ic"><svg width="18" height="18" viewBox="0 0 24 24"><path fill="#fff" d="M12 2a7 7 0 0 0-7 7c0 5 7 13 7 13s7-8 7-13a7 7 0 0 0-7-7zm0 9.5A2.5 2.5 0 1 1 12 6.5a2.5 2.5 0 0 1 0 5z"/></svg></div><div>420 Orchard Avenue, Suite 12<br>Brookfield, ST 00412</div></div>
<div class="abs info" style="left:384px"><div class="ic"><svg width="20" height="20" viewBox="0 0 24 24"><circle cx="12" cy="12" r="8" stroke="#fff" stroke-width="2" fill="none"/><path d="M12 7v5l3 2" stroke="#fff" stroke-width="2" fill="none"/></svg></div><div>Mon,wed,Fri : 8.30am-5.00pm<br>Tue-Thu : 9am-6.00pm</div></div>
<div class="abs info" style="left:686px"><div class="ic"><svg width="18" height="14" viewBox="0 0 18 14"><rect x="1" y="1" width="16" height="12" rx="1" fill="#fff"/><path d="M1 2l8 6 8-6" stroke="#f0246d" stroke-width="1.5" fill="none"/></svg></div><div>hello@visitwell.example</div></div>
<div class="abs info" style="left:953px"><div class="ic"><svg width="18" height="18" viewBox="0 0 24 24"><path fill="#fff" d="M6.6 10.8a15 15 0 0 0 6.6 6.6l2.2-2.2c.3-.3.7-.4 1-.2 1.1.4 2.3.6 3.6.6.6 0 1 .4 1 1V20c0 .6-.4 1-1 1A17 17 0 0 1 3 4c0-.6.4-1 1-1h3.5c.6 0 1 .4 1 1 0 1.3.2 2.5.6 3.6.1.3 0 .7-.2 1z"/></svg></div><div>(555) 204-7730</div></div>

<!-- footer -->
<div class="abs fcol" style="left:103px"><h4>Quick Links</h4><ul><li>Home</li><li>Product</li><li>Pricing</li><li>Blog</li><li>FAQ</li><li>Contact us</li></ul></div>
<div class="abs fcol" style="left:292px"><h4>Services</h4><ul><li>Lorem ipsum dolor sit amet</li><li>Lorem ipsum dolor sit amet</li><li>Lorem ipsum dolor sit amet</li></ul></div>
<div class="abs fcol" style="left:553px"><h4>Other Links</h4><ul><li>Terms &amp; Conditions</li><li>Privacy Policy</li></ul></div>
<div class="abs fcol" style="left:786px"><h4>Newsletter</h4></div>
<div class="abs news-input">Email Address</div>
<div class="abs news-btn"><svg width="18" height="18" viewBox="0 0 24 24"><path fill="#fff" d="M2 11l20-9-9 20-2-9z"/></svg></div>

<div class="abs bottom">
  <div class="copy">© Copyrights.2020.The Company Name.All Rights Reserved</div>
  <div class="connect">Connect With Us : <i></i><i></i><i></i><i></i></div>
  <div class="code">C28</div>
</div>

</body>
</html>
```